Business Card Design Project

We're looking for a unique business card design that stands out from the rest, using the brand and logo we've already developed.
Two-sided design please.
Quillmark Media (www.quillmarkmedia.com.au) is a digitally-focused advertising agency that has produces results-driven campaigns. As a result, we'd like our business card to reflect our innovative approach.
Size, shape, orientation, etc, are all flexible (providing the print costs don't become ridiculous or we have to sit there with tiny scissors!).
Business card should include space for name, title, email, mobile, landline and address.
Industry/Entity Type
Advertising
Look and feel

```html
<!DOCTYPE html>
<html lang="en">
<head>
<meta charset="utf-8">
<title>Quillmark Media – Business Card</title>
<link rel="stylesheet" href="https://fonts.googleapis.com/css2?family=Oswald:wght@400;500&display=swap">
<style>
  :root {
    --brand-red: #ec1c24;
    --paper-white: #ffffff;
    --ink-black: #111111;
    --accent-orange: #f7882f;
    --edge-blue: #1f74bd;
    --backdrop: #e7e5e2;
  }
  html, body {
    margin: 0;
    padding: 0;
    width: 1200px;
    height: 1200px;
    overflow: hidden;
    background: var(--backdrop);
  }
  .canvas {
    position: relative;
    width: 1200px;
    height: 1200px;
  }
  .card {
    position: absolute;
    display: block;
  }
  .card-front { left: 54px; top: 48px; }
  .card-back  { left: 36px; top: 624px; }
  .brand-name {
    font-family: "Oswald", sans-serif;
    font-weight: 400;
    fill: var(--ink-black);
  }
  .field-label {
    font-family: "Oswald", sans-serif;
    font-weight: 500;
    font-size: 34px;
    fill: var(--ink-black);
  }
</style>
</head>
<body>
<main class="canvas">

  <!-- Front side -->
  <svg class="card card-front" width="1074" height="528" viewBox="0 0 1074 528" aria-label="Card front">
    <defs>
      <clipPath id="front-shape">
        <rect width="1074" height="528" rx="42" ry="42"/>
      </clipPath>
    </defs>
    <g clip-path="url(#front-shape)">
      <rect class="front-base" width="1074" height="528" fill="var(--brand-red)"/>
      <path class="front-swoop" fill="var(--paper-white)"
            d="M0,0 H1074 V20 L1044,36 L924,198 L920,66 C760,300 600,360 462,360 C300,360 120,260 0,66 Z"/>
    </g>
    <g class="front-brand">
      <circle class="brand-dot" cx="172" cy="222" r="22" fill="var(--accent-orange)"/>
      <text class="brand-name" x="212" y="262" font-size="108">Quillmark Media</text>
    </g>
  </svg>

  <!-- Back side -->
  <svg class="card card-back" width="1062" height="534" viewBox="0 0 1062 534" aria-label="Card back">
    <defs>
      <clipPath id="back-shape">
        <rect width="1062" height="534" rx="42" ry="42"/>
      </clipPath>
    </defs>
    <g clip-path="url(#back-shape)">
      <rect class="back-base" width="1062" height="534" fill="var(--paper-white)"/>
      <polygon class="back-edge-stripe" points="736,0 746,0 620,534 610,534" fill="var(--edge-blue)"/>
      <polygon class="back-brand-panel" points="746,0 1062,0 1062,534 620,534" fill="var(--brand-red)"/>
    </g>
    <g class="contact-fields">
      <text class="field-label" x="204" y="114">NAME:</text>
      <text class="field-label" x="204" y="162">TITLE:</text>
      <text class="field-label" x="204" y="210">EMAIL:</text>
      <text class="field-label" x="204" y="312">MOBILE:</text>
      <text class="field-label" x="204" y="366">LANDLINE:</text>
      <text class="field-label" x="204" y="420">ADDRESS:</text>
    </g>
    <g class="back-brand" transform="translate(820,40) rotate(90)">
      <text class="brand-name" x="0" y="0" font-size="80">Quillmark Media</text>
    </g>
  </svg>

</main>
</body>
</html>
```